Halvik - consultancy website

I need a new design for my webpage/presence [to be functioning with Wordpress - I have a programmer to set it up but not the design idea].
My company is Halvik - a consultancy firm focused on growth management for Swedish SME's primarily;. We call it Leadership toolkit for firms on the rise, kind of a doctor helping small become big. Contentwise, its a simple frontpage + 3-4 subpages with content re company/myself/focus etc. The new site should communicate a fresh, trustworthy take yet simple and functional on all devices [i.e. think UI compatible for mobile/tablet]. Current building parts/form elements are
a) existing logo and text elements
b) existing pictures
c) the yellowish color
colours and new ideas on pictures/positioning are welcome. I prefer a 'full width page' solution with centralised text elements but that's all up to you to suggest. Current site is a quickfix made by myself - now I'm moving it to a new platform so want to take the opportunity to make it
Nothing superspecial as it is a 2-man show; on the other hand I still want to have a modern & fresh reflection of my brand in digital environments. Help me out!
www.halvik-demo.se
Best
Lina Bergqvist

```html
<!DOCTYPE html>
<html lang="en">
<head>
<meta charset="utf-8">
<title>Halvik – Services</title>
<link href="https://fonts.googleapis.com/css2?family=Arimo:wght@400;700&family=Gelasio:wght@400&family=Open+Sans:wght@400;600&display=swap" rel="stylesheet">
<style>
:root{
  --accent:#f0a23a;
  --ink:#222;
  --text:#666;
  --nav:#222;
  --band:#2b2b2b;
  --cta:#333333;
  --footer:#1f1f1f;
  --footer-deep:#181818;
  --rule:#d9d9d9;
  --white:#fff;
  --social-a:#35509a;
  --social-b:#3fb0e3;
  --social-c:#dd4b39;
}
*{margin:0;padding:0;box-sizing:border-box}
html,body{width:960px;height:1200px;overflow:hidden;background:var(--white)}
body{position:relative;font-family:"Arimo",Arial,sans-serif;color:var(--ink)}
.abs{position:absolute}

.brand{left:78px;top:20px}
.brand-name{font-family:"Gelasio",Georgia,serif;font-size:42px;line-height:1;color:var(--ink)}
.brand-tag{font-family:"Gelasio",Georgia,serif;font-size:12.5px;margin-top:6px;margin-left:2px;color:var(--ink)}
.nav a{position:absolute;top:48px;font-size:11.5px;color:var(--nav);text-decoration:none}
.nav a.current{color:var(--accent)}
.nav-underline{left:648px;top:69px;width:85px;height:1.5px;background:var(--accent)}

.crumbs{left:0;top:106px;width:960px;height:42px;background:var(--band);color:var(--white);font-size:11.5px;padding:16px 0 0 78px}
.crumbs b{color:var(--accent)}

.section-title{left:0;width:928px;top:201px;text-align:center;font-size:21px;font-weight:700}
.intro{left:76px;width:806px;top:245px;text-align:center;font-size:11.5px;line-height:16.5px;color:var(--text)}

.svc-icon{width:76px;height:76px;border-radius:50%;border:1px solid #444;top:330px;display:flex;align-items:center;justify-content:center}
.svc-icon.active{border-color:var(--accent)}
.svc-rail{left:76px;top:422px;width:808px;height:1px;background:var(--rule)}
.rail-btn{top:416px;width:13px;height:13px;border:1px solid var(--rule);background:var(--white);font-size:8px;color:#aaa;text-align:center;line-height:11px}
.rail-mark{left:183px;top:421px;width:55px;height:2px;background:var(--accent)}
.rail-tip{left:206px;top:422px;width:0;height:0;border-left:5px solid transparent;border-right:5px solid transparent;border-top:5px solid var(--accent)}
.svc-label{top:437px;width:180px;text-align:center;font-size:11.5px;color:var(--ink)}
.svc-label.active{color:var(--accent)}

.detail-title{left:147px;top:526px;font-size:18px;line-height:25px;color:var(--ink)}
.detail-title strong{display:block;font-size:19px}
.detail-text{left:148px;top:593px;width:400px;font-size:11.5px;line-height:16.5px;color:var(--text)}
.detail-chart{left:653px;top:530px}

.cta{left:0;top:752px;width:960px;height:224px;background:var(--cta);text-align:center;color:var(--white)}
.cta h2{margin-top:60px;font-size:24px;letter-spacing:3.5px;font-weight:700}
.cta p{margin-top:8px;font-size:11px;letter-spacing:2px;font-weight:700}
.cta-btn{display:inline-block;margin-top:20px;width:130px;height:34px;border:1.5px solid var(--white);border-radius:3px;line-height:31px;font-size:11.5px;font-weight:700;color:var(--white)}

.footer{left:0;top:976px;width:960px;height:184px;background:var(--footer);font-family:"Open Sans",Arial,sans-serif;color:var(--white)}
.foot-title{top:30px;font-size:11.5px;letter-spacing:.3px}
.foot-divider{top:34px;width:1px;height:124px;background:#3a3a3a}
.tile{top:69px;width:58px;height:75px;text-align:center;font-size:10px}
.tile .dot{width:32px;height:32px;border-radius:50%;background:rgba(255,255,255,.18);margin:11px auto 0}
.tile .count{margin-top:16px}
.mail-text{left:428px;top:68px;width:190px;font-size:9px;line-height:14px;color:#999;letter-spacing:.3px}
.mail-input{left:429px;top:105px;width:159px;height:22px;background:var(--white);font-size:8.5px;color:#999;padding:6px 0 0 12px;letter-spacing:.3px}
.mail-go{left:588px;top:105px;width:26px;height:22px;background:var(--accent);display:flex;align-items:center;justify-content:center}
.mail-note{left:429px;top:135px;font-size:8.5px;color:#777;letter-spacing:.3px}
.menu{left:778px;top:66px;list-style:none;font-size:9px;line-height:17px}

.legal{left:0;top:1160px;width:960px;height:40px;background:var(--footer-deep);text-align:center;font-size:9px;color:#777;padding-top:15px}
</style>
</head>
<body>

<header>
  <div class="abs brand">
    <div class="brand-name">Halvik.</div>
    <div class="brand-tag">Leadership toolkit for firms on the rise</div>
  </div>
  <nav class="nav">
    <a style="left:491px">Home</a>
    <a style="left:573px">About Us</a>
    <a class="current" style="left:664px">Services</a>
    <a style="left:758px">Gallery</a>
    <a style="left:836px">Contact Us</a>
  </nav>
  <div class="abs nav-underline"></div>
</header>

<div class="abs crumbs">Home &nbsp;&gt;&gt;&nbsp; <b>Services</b></div>

<h1 class="abs section-title">Our Services</h1>
<p class="abs intro">Donec eu viverra odio, eu cursus orci. Vestibulum id imperdiet est, non dictum leo. Aenean dictum nunc ex, quis vehicula dolor posuere id. Donec luctus luctus nisl, id porta turpis. Class aptent taciti sociosqu ad litora torquent per conubia nostra, per inceptos himenaeos. Curabitur metus libero, suscipit pretium erat sed, cursus faucibus erat. Vestibulum ante ipsum primis in</p>

<div class="abs svc-icon active" style="left:172px">
  <svg width="36" height="28" viewBox="0 0 36 28"><path d="M1 1v26h34" fill="none" stroke="#f0a23a" stroke-width="2.5"/><rect x="7" y="15" width="4" height="9" fill="#f0a23a"/><rect x="13" y="9" width="4" height="15" fill="#f0a23a"/><rect x="19" y="12" width="4" height="12" fill="#f0a23a"/><rect x="25" y="6" width="4" height="18" fill="#f0a23a"/></svg>
</div>
<div class="abs svc-icon" style="left:350px">
  <svg width="40" height="34" viewBox="0 0 40 34"><path d="M3 11h10l16-9v28l-16-9H3z" fill="#333"/><path d="M8 21l3 10h5l-3-10z" fill="#333"/><path d="M33 9c3 2 3 10 0 12" fill="none" stroke="#333" stroke-width="2.5"/></svg>
</div>
<div class="abs svc-icon" style="left:528px">
  <svg width="30" height="32" viewBox="0 0 30 32"><rect x="1" y="5" width="28" height="26" fill="none" stroke="#333" stroke-width="2.5"/><rect x="1" y="5" width="28" height="6" fill="#333"/><rect x="7" y="1" width="3" height="7" fill="#333"/><rect x="20" y="1" width="3" height="7" fill="#333"/><path d="M3 17h24M3 22h24M3 27h24M8 11v19M15 11v19M22 11v19" stroke="#333" stroke-width="1.6"/></svg>
</div>
<div class="abs svc-icon" style="left:713px">
  <svg width="40" height="32" viewBox="0 0 40 32"><rect x="2" y="12" width="7" height="17" fill="#333"/><path d="M11 13l7-11c3 0 4 2 3 5l-2 5h16c3 0 3 5 0 5h-9v3c0 2-2 3-3 3v3c-1 2-3 3-4 3H11z" fill="none" stroke="#333" stroke-width="2.5" stroke-linejoin="round"/></svg>
</div>

<div class="abs svc-rail"></div>
<div class="abs rail-btn" style="left:76px">‹</div>
<div class="abs rail-btn" style="left:871px">›</div>
<div class="abs rail-mark"></div>
<div class="abs rail-tip"></div>

<div class="abs svc-label active" style="left:121px">Growth Management</div>
<div class="abs svc-label" style="left:299px">Corporate Communication</div>
<div class="abs svc-label" style="left:477px">Project Management</div>
<div class="abs svc-label" style="left:662px">Concepetualizing</div>

<h2 class="abs detail-title">Growth<strong>Management</strong></h2>
<p class="abs detail-text">Pellentesque feugiat lacus a leo faucibus facilisis. Sed non tristique massa. Integer molestie, nunc quis sollicitudin condimentum.Pellentesque feugiat lacus a leo faucibus facilisis. Sed non tristique massa. Integer molestie, nunc quis sollicitudin condimentum.</p>

<svg class="abs detail-chart" width="164" height="124" viewBox="0 0 164 124">
  <path d="M5 0v119h159" fill="none" stroke="#f0a23a" stroke-width="10"/>
  <rect x="31" y="62" width="21" height="42" fill="#f0a23a"/>
  <rect x="61" y="21" width="21" height="83" fill="#f0a23a"/>
  <rect x="92" y="42" width="21" height="62" fill="#f0a23a"/>
  <rect x="122" y="11" width="21" height="93" fill="#f0a23a"/>
</svg>

<section class="abs cta">
  <h2>DONEC EU VIVERRA ODIO, EU CURSUS ORCI.</h2>
  <p>IN VARIUS VENENATIS ELIT, A PLACERAT LACUS. MAURIS SUSCIPIT</p>
  <span class="cta-btn">CONTACT NOW</span>
</section>

<footer class="abs footer">
  <div class="abs foot-title" style="left:78px">Let's Connect</div>
  <div class="abs tile" style="left:78px;background:var(--social-a)"><div class="dot"></div><div class="count">2598</div></div>
  <div class="abs tile" style="left:142px;background:var(--social-b)"><div class="dot"></div><div class="count">4576</div></div>
  <div class="abs tile" style="left:206px;background:var(--social-c)"><div class="dot"></div><div class="count">1269</div></div>

  <div class="abs foot-divider" style="left:350px"></div>

  <div class="abs foot-title" style="left:428px">Mailing List</div>
  <p class="abs mail-text">Sign up for our mailing list to get latest updates and offers.</p>
  <div class="abs mail-input">Email address</div>
  <div class="abs mail-go"><svg width="10" height="8" viewBox="0 0 10 8"><path d="M1 4l3 3 5-6" fill="none" stroke="#fff" stroke-width="1.8"/></svg></div>
  <div class="abs mail-note">We respect your privacy</div>

  <div class="abs foot-divider" style="left:700px"></div>

  <div class="abs foot-title" style="left:778px">Menu</div>
  <ul class="abs menu">
    <li>Home</li><li>About Us</li><li>Services</li><li>Gallery</li><li>Contact Us</li>
  </ul>
</footer>

<div class="abs legal">© Copyrights 2015 All Rights Reserved</div>

</body>
</html>
```